Fire and Building compliance company needs website

A professional website is needed for Thornbury Fire and Security 2012 , company profile attached- we have a website but it is old and needs replacing (in fact we can not access it at present).

We are also looking at getting logo redesigned and will probably change to a flame type graphic with the letters TFS and then Fire and Building Compliance (bellow TFS).

Page should fit inside typical screen size (not have to scroll down to see page).
Be made in Joomla 2.5

search words- Wanganui, fire alarm, building compliance, building warrant of fitness,BWOF, burglar alarm systems, LPG refilling,fire extinguishers, emergency lighting.

```html
<!DOCTYPE html>
<html lang="en">
<head>
<meta charset="utf-8">
<title>Thornbury Fire and Security</title>
<link href="https://fonts.googleapis.com/css2?family=Ubuntu:wght@400;500;700&family=Open+Sans:wght@400;600;700&display=swap" rel="stylesheet">
<style>
:root{
  --orange:#fdb10f;
  --orange-dark:#f39a00;
  --orange-text:#f5a400;
  --ink:#222;
  --body:#555;
  --muted:#999;
  --panel:#f7f7f7;
  --black:#111;
  --line:#2b2b2b;
  --white:#fff;
}
*{box-sizing:border-box;margin:0;padding:0}
html,body{width:979px;height:1200px;overflow:hidden;background:var(--white)}
body{position:relative;font-family:"Open Sans",Arial,sans-serif;color:var(--body)}
a{color:inherit}
.abs{position:absolute}

/* header */
.header{left:0;top:0;width:979px;height:160px;background:linear-gradient(#fff 0,#fff 60%,#e9e9e9 100%)}
.brand{left:36px;top:62px;display:flex;align-items:center;gap:10px}
.brand-mark{width:22px;height:22px;background:var(--orange-dark)}
.brand-name{font-family:"Ubuntu",sans-serif;font-weight:500;font-size:20px;line-height:1;color:var(--ink);white-space:nowrap}
.search{left:629px;top:35px;display:flex;align-items:center;gap:6px;font-size:11px;color:#444}
.search-field{width:163px;height:26px;border:1px solid #ddd;background:#fff;margin-left:8px}
.search-go{width:34px;height:26px;border-radius:4px;background:var(--orange);color:#fff;font-weight:700;font-size:13px;display:flex;align-items:center;justify-content:center}
.nav{left:332px;top:84px;width:609px;height:78px;background:#fff;box-shadow:0 -2px 4px rgba(0,0,0,.08);border-top:3px solid #e4e4e4}
.nav-item{position:absolute;top:35px;font-family:"Ubuntu",sans-serif;font-weight:500;font-size:16px;color:var(--ink)}
.nav-item::before{content:"";position:absolute;top:-29px;left:50%;margin-left:-4px;border:4px solid transparent;border-top:5px solid var(--orange)}

/* showcase */
.band{left:0;top:173px;width:979px;height:393px;background:var(--orange)}
.slide{left:28px;top:150px;width:627px;height:416px;background:linear-gradient(180deg,#3f5a2c 0%,#55683f 22%,#6a6a66 40%,#4b4b4b 70%,#3a3a3a 100%)}
.dots{left:268px;top:545px;display:flex;gap:16px}
.dots span{width:13px;height:13px;border-radius:50%;background:#e8e8e8}
.feature{left:655px;width:324px;padding:22px 0 0 17px;color:#fff;border-bottom:1px solid rgba(0,0,0,.06)}
.feature:nth-of-type(odd){background:linear-gradient(#fdb616,#f7a707)}
.feature-title{font-family:"Ubuntu",sans-serif;font-weight:700;font-size:25px;line-height:1;letter-spacing:-1.2px;white-space:nowrap}
.feature-sub{font-size:10px;letter-spacing:.3px;opacity:.85;line-height:1.2;text-transform:uppercase}
.feature-more{display:flex;align-items:center;gap:12px;margin-top:9px;font-size:11px;font-weight:600;color:#5a3b00}
.feature-more i{width:18px;height:12px;background:repeating-linear-gradient(90deg,rgba(255,255,255,.55) 0 3px,transparent 3px 5px)}

/* content */
.content{left:0;top:566px;width:979px;height:306px;background:linear-gradient(#ebebeb,#fff 40px)}
.heading{display:flex;align-items:flex-start;gap:8px}
.heading-icon{width:44px;height:44px}
.heading-title{font-family:"Ubuntu",sans-serif;font-size:29px;line-height:1;letter-spacing:-1px;color:#8a8a8a;white-space:nowrap}
.heading-title b{color:var(--orange-text);font-weight:700}
.heading-sub{font-size:11px;color:#f2c060;letter-spacing:.3px;margin-top:1px}
.thumb{left:64px;top:667px;width:166px;height:96px;border:1px solid #ccc;padding:3px;background:#fff}
.thumb div{width:100%;height:100%;background:linear-gradient(#4e6938,#6d7458 45%,#7b7b78)}
.intro{left:246px;top:655px;width:382px;font-size:13.5px;line-height:19px;color:#555}
.intro b{color:var(--orange-text);font-weight:700}
.links{left:72px;top:776px;width:560px;list-style:none;font-size:12px}
.links li{height:28px;display:flex;gap:13px;color:#555}
.links li::before{content:"»";color:#444}
.links a{text-decoration:underline}
.news-date{width:18px;height:18px;border:1px solid #8aa;background:#eef4f8;border-radius:2px}
.news-title{color:var(--orange-text);font-weight:700;font-size:13px}
.news-text{left:663px;top:677px;width:230px;font-size:12px;line-height:18px;color:#222;text-decoration:underline}
.news-more{left:840px;top:716px;font-size:12px;color:var(--orange-text);display:flex;align-items:center;gap:6px}
.news-more i{width:13px;height:13px;border-radius:50%;background:#333}
.tags-title{left:657px;top:737px;font-size:16px;color:#444}
.tags{left:657px;top:768px;width:260px;display:flex;flex-wrap:wrap;gap:6px 6px}
.tag{height:25px;padding:0 9px;background:#dcdcdc;border:1px solid #cfcfcf;font-size:9.5px;color:#555;display:flex;align-items:center}
.tag.active{background:#4b4b4b;color:#fff}

/* services */
.services{left:38px;top:873px;width:903px;height:238px;background:var(--panel)}
.service{position:absolute;top:0;width:242px}
.service-head{height:47px;background:var(--black);color:#fff;font-family:"Ubuntu",sans-serif;font-size:19px;letter-spacing:-.5px;display:flex;align-items:center;justify-content:center;text-transform:uppercase}
.service-head b{font-weight:700;margin-right:6px}
.service-head span{color:#bbb;font-weight:400}
.service-icon{position:absolute;top:64px;left:14px;width:56px;height:56px}
.service-link{position:absolute;top:79px;left:91px;font-size:12px;line-height:18px;color:#111;text-decoration:underline}
.service-title{position:absolute;top:140px;left:21px;font-size:13px;font-weight:700;color:var(--orange-text);white-space:nowrap}
.service-text{position:absolute;top:160px;left:21px;width:220px;font-size:12px;line-height:18px;color:#555}

/* footer */
.footer-rule{left:38px;top:1113px;width:903px;height:5px;background:var(--line)}
.footer-nav{left:0;top:1136px;width:979px;text-align:center;font-size:12.5px;color:#555;letter-spacing:.2px}
.footer-copy{left:0;top:1158px;width:979px;text-align:center;font-size:11px;color:#666}
</style>
</head>
<body>

<header class="abs header"></header>
<div class="abs brand"><span class="brand-mark"></span><span class="brand-name">Thornbury Fire and Security</span></div>

<form class="abs search"><span>Search the site</span><span class="search-field"></span><span class="search-go">GO</span></form>

<nav class="abs nav">
  <a class="nav-item" style="left:38px">HOME</a>
  <a class="nav-item" style="left:134px">ABOUT</a>
  <a class="nav-item" style="left:240px">SERVICES</a>
  <a class="nav-item" style="left:359px">PRODUCTS</a>
  <a class="nav-item" style="left:495px">CONTACTS</a>
</nav>

<div class="abs band"></div>
<div class="abs slide" role="img" aria-label="Fire training demonstration: a burning training pan on a wet car park with a gas cylinder and hose"></div>
<div class="abs dots"><span></span><span></span><span></span><span></span><span></span></div>

<div class="abs feature" style="top:173px;height:111px">
  <div class="feature-title">BUILDING COMPLIANCE</div>
  <div class="feature-sub">Lorem ipsum dolor sit amet, lorem</div>
  <div class="feature-more"><i></i>READ MORE</div>
</div>
<div class="abs feature" style="top:284px;height:101px">
  <div class="feature-title">FIRE ALARMS -Training</div>
  <div class="feature-sub">Quisque ut magna et nisi</div>
  <div class="feature-more"><i></i>READ MORE</div>
</div>
<div class="abs feature" style="top:385px;height:99px">
  <div class="feature-title">INNOVATION</div>
  <div class="feature-sub">Lorem ipsum dolor sit amet, lorem</div>
  <div class="feature-more"><i></i>READ MORE</div>
</div>
<div class="abs feature" style="top:484px;height:82px;padding-top:9px">
  <div class="feature-title">GAS PACKING SYSTEMS</div>
  <div class="feature-sub">Lorem ipsum dolor sit amet, lorem</div>
  <div class="feature-more"><i></i>READ MORE</div>
</div>

<main class="abs content"></main>

<section class="abs heading" style="left:57px;top:594px">
  <svg class="heading-icon" viewBox="0 0 44 44"><rect x="1" y="3" width="40" height="40" rx="5" fill="#6d6d6d"/><rect x="4" y="6" width="34" height="34" rx="3" fill="#f2f2f2"/><path d="M10 22l8 8 20-24" fill="none" stroke="#666" stroke-width="6" stroke-linecap="round" stroke-linejoin="round"/></svg>
  <div><div class="heading-title"><b>WELCOME</b>TO OUR COMPANY!</div><div class="heading-sub">LOREM IPSUM DOLOR SIT AMET, LOREM</div></div>
</section>
<div class="abs thumb"><div role="img" aria-label="Staff running a fire extinguisher training session outdoors"></div></div>
<p class="abs intro"><b>Thornbury Fire &amp; Security</b> is a locally owned and operated fire protection company. Since 1978 we have evolved and developed to suit the demands of our clients and the 1992 Building Compliance Act. This ability to alter and change as required means that we are now viewed as an innovative and contemporary company.</p>
<ul class="abs links">
  <li><a>Nam eu nulla. Donec lobortis purus vel urna. Nunc laoreet lacinia nunc. In volutpat sodales</a></li>
  <li><a>ipsum. Sed vestibulum. Integer in ante. Sed posuere ligula rhoncus erat. Fusce urna dui,</a></li>
  <li><a>sollicitudin ac, pulvinar quis, tincidunt et, risus. Quisque a nunc eget nibh interdum fringilla.</a></li>
</ul>

<section class="abs heading" style="left:657px;top:594px">
  <svg class="heading-icon" viewBox="0 0 44 44"><rect x="1" y="3" width="40" height="40" rx="5" fill="#6d6d6d"/><rect x="4" y="6" width="34" height="34" rx="3" fill="#f2f2f2"/><path d="M10 22l8 8 20-24" fill="none" stroke="#666" stroke-width="6" stroke-linecap="round" stroke-linejoin="round"/></svg>
  <div><div class="heading-title"><b>NEWS</b>UPDATES</div><div class="heading-sub">LOREM IPSUM SIT AMET, LOREM</div></div>
</section>
<div class="abs" style="left:663px;top:652px;display:flex;gap:12px;align-items:center"><span class="news-date"></span><span class="news-title">Duis tempor ipsum vitae diam.</span></div>
<p class="abs news-text">Morbi volutpat leo in ligula. Integer vel magna. Quisque ut magna et nisi</p>
<div class="abs news-more">more <i></i></div>
<div class="abs tags-title">Tags</div>
<div class="abs tags">
  <span class="tag">Wanganui</span><span class="tag active">Fire Alarm</span><span class="tag">Building Compliance</span>
  <span class="tag">Building Warrant of Fitness</span><span class="tag">Fire Extinguishers</span>
  <span class="tag">Burglar Alarm Systems</span><span class="tag">LPG Refilling</span><span class="tag">BWOF</span>
</div>

<section class="abs services">
  <article class="service" style="left:0">
    <div class="service-head"><b>FIRE</b><span>ALARMS</span></div>
    <svg class="service-icon" viewBox="0 0 56 56"><ellipse cx="22" cy="20" rx="20" ry="15" fill="#3d8fd6"/><path d="M10 31l-4 10 12-7z" fill="#3d8fd6"/><ellipse cx="36" cy="32" rx="17" ry="12" fill="#6cc04a"/><path d="M44 41l6 8-12-5z" fill="#6cc04a"/></svg>
    <a class="service-link">Inter vel magna, sagittis.<br>Fusce elit ligula</a>
    <div class="service-title">Fusce interdum. Maecenas</div>
    <p class="service-text">Morbi volutpat leo in ligula. Inter vel magna, sagittis. Fusce elit ligula, Aenean. Sed laoreet.</p>
  </article>
  <article class="service" style="left:312px">
    <div class="service-head"><b>FIRE TECH</b><span>TRAINING</span></div>
    <svg class="service-icon" viewBox="0 0 56 56"><g fill="#b5b5b5"><circle cx="28" cy="28" r="17"/><rect x="24" y="4" width="8" height="48" rx="2"/><rect x="4" y="24" width="48" height="8" rx="2"/><rect x="24" y="4" width="8" height="48" rx="2" transform="rotate(45 28 28)"/><rect x="24" y="4" width="8" height="48" rx="2" transform="rotate(-45 28 28)"/></g><circle cx="28" cy="28" r="7" fill="#f7f7f7"/></svg>
    <a class="service-link">Inter vel magna, sagittis.<br>Fusce elit ligula</a>
    <div class="service-title">Maecenas non orci lorem ipsum</div>
    <p class="service-text">Morbi volutpat leo in ligula. Inter vel magna, sagittis. Fusce elit ligula, Aenean. Sed laoreet.</p>
  </article>
  <article class="service" style="left:619px">
    <div class="service-head"><b>SALE</b><span>SERVICES?</span></div>
    <svg class="service-icon" viewBox="0 0 56 56"><circle cx="28" cy="28" r="25" fill="#ddd"/><circle cx="28" cy="28" r="21" fill="#fff" stroke="#ccc"/><path d="M28 12v16l10 6" fill="none" stroke="#555" stroke-width="2.5" stroke-linecap="round"/><path d="M28 28l-9 9" stroke="#d22" stroke-width="1.2"/></svg>
    <a class="service-link">Inter vel magna, sagittis.<br>Fusce elit ligula</a>
    <div class="service-title">Fusce interdum. Maecenas</div>
    <p class="service-text">Morbi volutpat leo in ligula. Inter vel magna, sagittis. Fusce elit ligula, Aenean. Sed laoreet.</p>
  </article>
</section>

<div class="abs footer-rule"></div>
<nav class="abs footer-nav">HOME | ABOUT | SERVICES | PRODUCTS | SPONSORSHIP| INFO | CONTACTS</nav>
<p class="abs footer-copy">Copyright 2013 © Thornbury Fire and Security (TFS)</p>

</body>
</html>
```